Vorn upkeep KT Solar Venture

Solar power system install
Services and maintenance
wiring, Rewinding and Renovation
Switch Board Upgrade
Power and lighting point
t doesn’t matter how much you spend on quality parts, your solar system will let you down if your design and installation are sub-par. Have your solar system tailored and installed by our Master Electrician and Bright Grid Guild Accredited team.

Target Market(s)

sales and installed

Industry/Entity Type

Solar install and retailer

Contact Information for Business Card

Name , Email, Phone Number ,Business address,

Font styles to use
Serif

Colors
0054AA
0677BA
7BADD7
CADEEF
E8F1F8

Requirements
Must have
• clear and bright
Nice to have
• new design
Should not have
• unclear pictures

```html
<!DOCTYPE html>
<html lang="en">
<head>
<meta charset="utf-8">
<title>Vorn upkeep – KT Solar Venture business card</title>
<link href="https://fonts.googleapis.com/css2?family=Roboto:wght@400;500;700&family=Roboto+Condensed:wght@700&display=swap" rel="stylesheet">
<style>
  :root {
    --bg: #2c2c2c;
    --blue-deep: #0054AA;
    --blue-mid: #0677BA;
    --blue-light: #7BADD7;
    --blue-pale: #CADEEF;
    --blue-wash: #E8F1F8;
    --green: #3a9a2e;
    --green-bright: #8dc63f;
    --sun: #f2b705;
    --white: #ffffff;
    --panel-white: #eeeeee;
  }
  * { margin: 0; padding: 0; box-sizing: border-box; }
  html, body {
    width: 1200px; height: 1138px; overflow: hidden;
    background: var(--bg);
    font-family: "Roboto", Arial, sans-serif;
  }
  .card {
    position: absolute;
    width: 623px; height: 376px;
    border-radius: 14px;
    overflow: hidden;
  }
  .card-front { left: 274px; top: 185px; }
  .card-back  { left: 276px; top: 607px; }
  .card-art { position: absolute; inset: 0; width: 100%; height: 100%; }

  .brand-name {
    position: absolute;
    font-family: "Roboto Condensed", "Roboto", sans-serif;
    font-weight: 700;
    letter-spacing: 0.5px;
    line-height: 1.15;
    text-transform: uppercase;
  }
  .card-front .brand-name {
    left: 402px; top: 84px;
    font-size: 24px; color: var(--white);
  }
  .card-back .brand-name {
    left: 345px; width: 260px; top: 206px;
    font-size: 27px; color: var(--blue-deep); text-align: center;
  }

  .service-list {
    position: absolute; right: 34px; top: 230px;
    list-style: none; text-align: right;
    color: var(--white); font-size: 16px; line-height: 22.3px;
  }
  .service-list li::after { content: "\00AB"; margin-left: 10px; }

  .holder-name {
    position: absolute; left: 42px; top: 70px;
    color: var(--green-bright); font-size: 24px; font-weight: 500;
  }
  .holder-role {
    position: absolute; left: 42px; top: 101px;
    color: var(--white); font-size: 16px;
  }
  .address {
    position: absolute; left: 42px; top: 180px;
    color: var(--white); font-size: 16px; line-height: 24px; font-style: normal;
  }
  .contact-list {
    position: absolute; left: 42px; top: 235px;
    list-style: none; color: var(--white); font-size: 16px; line-height: 24px;
  }
  .contact-list li { display: flex; align-items: center; height: 24px; }
  .contact-list svg { width: 16px; height: 16px; margin-right: 16px; flex: none; }
</style>
</head>
<body>

<section class="card card-front" aria-label="Business card front">
  <svg class="card-art" viewBox="0 0 623 376" preserveAspectRatio="none">
    <defs>
      <linearGradient id="front-blue" x1="0" y1="0" x2="0" y2="1">
        <stop offset="0" stop-color="#004f9e"/>
        <stop offset="1" stop-color="#1a86d0"/>
      </linearGradient>
      <linearGradient id="panel-tone" x1="0" y1="0" x2="1" y2="1">
        <stop offset="0" stop-color="#6f7c92"/>
        <stop offset="0.35" stop-color="#b59a86"/>
        <stop offset="0.6" stop-color="#2e3550"/>
        <stop offset="1" stop-color="#1d2236"/>
      </linearGradient>
    </defs>
    <rect width="623" height="376" fill="url(#front-blue)"/>
    <path d="M0,0 L211,0 Q345,188 203,376 L0,376 Z" fill="url(#panel-tone)" role="img" aria-label="Photo of solar panels in sunlight"/>
    <path d="M211,0 Q345,188 203,376" fill="none" stroke="var(--green)" stroke-width="7"/>
    <circle cx="367" cy="98" r="28" fill="var(--sun)"/>
  </svg>
  <div class="brand-name">Vorn Upkeep<br>KT Solar Venture</div>
  <ul class="service-list">
    <li>Solar Power System Install</li>
    <li>Services &amp; Maintenance</li>
    <li>Switch Board Upgrade</li>
    <li>Power &amp; Lighting Point</li>
    <li>Wiring, Rewinding &amp; Renovation</li>
  </ul>
</section>

<section class="card card-back" aria-label="Business card back">
  <svg class="card-art" viewBox="0 0 623 376" preserveAspectRatio="none">
    <defs>
      <linearGradient id="back-blue" x1="0" y1="0" x2="0" y2="1">
        <stop offset="0" stop-color="#00519f"/>
        <stop offset="1" stop-color="#1a86d0"/>
      </linearGradient>
    </defs>
    <rect width="623" height="376" fill="url(#back-blue)"/>
    <path d="M384,0 Q246,188 388,376 L623,376 L623,0 Z" fill="var(--panel-white)"/>
    <path d="M384,0 Q246,188 388,376" fill="none" stroke="var(--green)" stroke-width="6"/>
    <circle cx="475" cy="140" r="48" fill="var(--sun)"/>
  </svg>

  <h1 class="holder-name">Dale Renner</h1>
  <p class="holder-role">Managing Director</p>
  <address class="address">88 Harbor Row, Lakeview,<br>Fairtown, US 100482</address>
  <ul class="contact-list">
    <li>
      <svg viewBox="0 0 16 16" aria-hidden="true"><path d="M2 6 Q8 1 14 6 L12 7.5 L10.5 5.8 H5.5 L4 7.5 Z M4.5 8 H11.5 L13 14 H3 Z" fill="var(--green-bright)"/></svg>
      555-014-2270
    </li>
    <li>
      <svg viewBox="0 0 16 16" aria-hidden="true"><rect x="1.5" y="3.5" width="13" height="9" fill="var(--green-bright)"/><path d="M1.5 3.5 L8 9 L14.5 3.5" fill="none" stroke="#0a5fae" stroke-width="1.2"/></svg>
      dale@vornupkeep.com
    </li>
    <li>
      <svg viewBox="0 0 16 16" aria-hidden="true"><circle cx="8" cy="8" r="6.5" fill="var(--green-bright)"/><path d="M1.5 8 H14.5 M8 1.5 V14.5 M8 1.5 Q3.5 8 8 14.5 M8 1.5 Q12.5 8 8 14.5" fill="none" stroke="#0a5fae" stroke-width="0.9"/></svg>
      www.vornupkeep.com
    </li>
  </ul>

  <div class="brand-name">Vorn Upkeep<br>KT Solar Venture</div>
</section>

</body>
</html>
```